Business Card for Vorla Parts Wholesale supplier

Hi There! I need a new business card for our company. We are specialized in selling Vorla parts, mostly we sell new LCD screens for Zelnar and Drelks. I would like to see that back in the design.

You can find the colors and logo's on our website: www.hartuvo.nl

Industry/Entity Type

Business

Contact Information for Business Card

My Details:
Tobias Lindqvist

Phone: 0031687203316
E-mail: Tobias@hartuvo.nl

Slogan: "Because Quality Matters"

Font styles to use
Sans Serif

Colors

Designer to choose colors to be used in the design.

Requirements
Must have
• A Black backside with the Hartuvo logo on it. The front side should be clean with only my contact details.
• But I'm also open for something really different or awesome!
Nice to have
• Remember that we are in the parts & repairing industry, So i'll be handing those business cards mainly to repair companies. Maybe you can do something with that thought :)

```html
<!DOCTYPE html>
<html lang="en">
<head>
<meta charset="utf-8">
<title>Hartuvo Business Card</title>
<link href="https://fonts.googleapis.com/css2?family=Roboto:wght@400;500;700&display=swap" rel="stylesheet">
<style>
  :root {
    --page-bg: #e4e4e4;
    --card-black: #1d1d1d;
    --card-black-soft: #2a2a2a;
    --card-white: #f7f7f7;
    --brand-orange: #ec6b1f;
    --ink: #1b1b1b;
    --ink-soft: #333333;
    --white: #ffffff;
  }
  * { margin: 0; padding: 0; box-sizing: border-box; }
  html, body {
    width: 1200px; height: 576px; overflow: hidden;
    background: var(--page-bg);
    font-family: "Roboto", Arial, sans-serif;
  }
  .canvas { position: relative; width: 1200px; height: 576px; }

  .card {
    position: absolute; top: 138px;
    width: 484px; height: 294px;
    border-radius: 11px; overflow: hidden;
    box-shadow: 0 3px 6px rgba(0,0,0,0.25);
  }

  /* Back side */
  .card-back { left: 82px; background: var(--card-black); }
  .card-back .backdrop {
    position: absolute; inset: 0;
    background:
      radial-gradient(ellipse 70% 55% at 62% 22%, #3a3a3a 0%, rgba(40,40,40,0) 70%),
      linear-gradient(160deg, #262626 0%, var(--card-black) 55%, #1a1a1a 100%);
  }
  .card-back .wordmark {
    position: absolute; left: 0; right: 0; top: 0; bottom: 0;
    display: flex; align-items: center; justify-content: center; gap: 12px;
  }
  .wordmark-square { width: 34px; height: 34px; background: var(--brand-orange); border-radius: 4px; }
  .card-back .wordmark-text {
    font-weight: 700; font-size: 46px; color: var(--white); letter-spacing: 0.5px;
  }

  /* Front side */
  .card-front { left: 602px; height: 292px; background: var(--card-white); }
  .card-front .accent-band {
    position: absolute; top: 0; right: 0; width: 58px; height: 100%;
    background: var(--brand-orange);
  }
  .card-front .wordmark {
    position: absolute; left: 18px; top: 26px;
    display: flex; align-items: center; gap: 9px;
  }
  .card-front .wordmark-square { width: 28px; height: 28px; }
  .card-front .wordmark-text { font-weight: 700; font-size: 36px; color: var(--ink); line-height: 1; }

  .holder { position: absolute; left: 24px; top: 167px; }
  .holder-name { font-weight: 700; font-size: 18px; color: var(--ink); line-height: 1.2; }
  .holder-role { font-size: 10.5px; color: var(--ink-soft); margin-top: 3px; }

  .contact-list { position: absolute; left: 24px; top: 221px; list-style: none; }
  .contact-item {
    display: flex; align-items: center; gap: 10px;
    font-size: 11.5px; color: var(--ink); height: 17px;
  }
  .contact-icon { width: 12px; height: 12px; fill: var(--brand-orange); flex: none; }
</style>
</head>
<body>
<main class="canvas">

  <section class="card card-back" aria-label="Card back">
    <div class="backdrop" role="img" aria-label="Dark close-up photo of a smartphone with a cracked screen"></div>
    <div class="wordmark">
      <span class="wordmark-square"></span>
      <span class="wordmark-text">hartuvo</span>
    </div>
  </section>

  <section class="card card-front" aria-label="Card front">
    <div class="accent-band"></div>
    <div class="wordmark">
      <span class="wordmark-square"></span>
      <span class="wordmark-text">hartuvo</span>
    </div>

    <div class="holder">
      <p class="holder-name">Tobias Lindqvist</p>
      <p class="holder-role">Managing Director</p>
    </div>

    <ul class="contact-list">
      <li class="contact-item">
        <svg class="contact-icon" viewBox="0 0 12 12" aria-hidden="true">
          <path d="M1 4 Q6 0.5 11 4 L10 5.5 L8 5 L8 4 Q6 3.2 4 4 L4 5 L2 5.5 Z"/>
          <path d="M3 6 L9 6 L10.5 11 L1.5 11 Z"/>
        </svg>
        <span>0031687203316</span>
      </li>
      <li class="contact-item">
        <svg class="contact-icon" viewBox="0 0 12 12" aria-hidden="true">
          <circle cx="6" cy="6" r="5" fill="none" stroke="#ec6b1f" stroke-width="1.1"/>
          <ellipse cx="6" cy="6" rx="2.2" ry="5" fill="none" stroke="#ec6b1f" stroke-width="1"/>
          <path d="M1 6 H11 M2 3.5 H10 M2 8.5 H10" stroke="#ec6b1f" stroke-width="0.9"/>
        </svg>
        <span>Tobias@hartuvo.nl</span>
      </li>
      <li class="contact-item">
        <svg class="contact-icon" viewBox="0 0 12 12" aria-hidden="true">
          <rect x="0.5" y="2.5" width="11" height="7.5"/>
          <path d="M0.8 2.8 L6 7 L11.2 2.8" fill="none" stroke="#f7f7f7" stroke-width="1"/>
        </svg>
        <span>www.hartuvo.nl</span>
      </li>
    </ul>
  </section>

</main>
</body>
</html>
```